Quillbrook Amusements App Interface Design

Start Up Company Quillbrook Amusements needs design and colour for its App interface. App for Zelvofon/Trunel/Trunel mini. App allows customers to connect to our self serve kiosk and browse and download entertainment content. Kiosks will be placed in international airport departure lounges initially. Final design should be a great looking, modern feel that keeps with the style of the rest of our elements. Screenshots attached.

Industry/Entity Type

Entertainment

```html
<!DOCTYPE html>
<html lang="en">
<head>
<meta charset="utf-8">
<title>Quillbrook Amusements – Title Detail</title>
<link rel="stylesheet" href="https://fonts.googleapis.com/css2?family=Barlow:wght@400;500;600;700&family=Barlow+Condensed:wght@600;700&display=swap">
<style>
:root{
  --navy-deep:#0a1f4a;
  --navy:#123a7a;
  --navy-mid:#1d4f9c;
  --bar-blue:#3a8fe3;
  --bar-blue-light:#4a9cec;
  --tab-blue:#3f90e2;
  --card-body:#0e2a5e;
  --white:#ffffff;
  --soft:#cfe0f7;
  --poster-a:#8a9bb0;
  --poster-b:#3e4c60;
}
*{box-sizing:border-box;margin:0;padding:0}
html,body{width:1200px;height:800px;overflow:hidden;background:var(--navy-deep)}
body{font-family:"Barlow",Arial,sans-serif;color:var(--white)}
.app{position:relative;width:1200px;height:800px;overflow:hidden;background:var(--navy-deep)}

.status-bar{position:absolute;top:0;left:0;right:0;height:24px;background:var(--bar-blue-light);
  display:flex;align-items:center;justify-content:space-between;padding:0 12px;font-size:13px;font-weight:500}
.status-bar .time{position:absolute;left:50%;transform:translateX(-50%)}

.nav-bar{position:absolute;top:24px;left:0;right:0;height:48px;background:var(--bar-blue);
  display:flex;align-items:center;justify-content:center}
.nav-bar .location{position:absolute;left:14px;font-size:13px;font-weight:600;letter-spacing:.3px}
.nav-bar .location b{font-weight:700;margin-right:6px}
.nav-bar .title{font-family:"Barlow Condensed",Arial,sans-serif;font-weight:700;font-size:24px;letter-spacing:1px}

.hero{position:absolute;top:72px;left:0;right:0;height:408px;
  background:radial-gradient(ellipse 50% 70% at 62% 10%,rgba(90,150,230,.55),transparent 70%),
  linear-gradient(180deg,var(--navy-mid) 0%,var(--navy) 45%,var(--navy-deep) 100%)}
.poster{position:absolute;left:70px;top:40px;width:200px;height:290px;
  background:linear-gradient(160deg,var(--poster-a) 0%,var(--poster-b) 100%);border:1px solid rgba(255,255,255,.25)}
.details{position:absolute;left:305px;top:40px;width:800px}
.details h1{font-family:"Barlow Condensed",Arial,sans-serif;font-size:40px;font-weight:700;letter-spacing:1px;line-height:1}
.details .meta{font-size:13px;margin-top:4px;color:var(--soft)}
.details .genre{font-size:17px;margin-top:18px}
.details .cast{font-size:17px;margin-top:4px}
.details .cast b{font-weight:700}
.details h2{font-size:16px;font-weight:700;margin-top:18px;letter-spacing:.5px}
.details .plot{font-size:17px;font-weight:600;margin-top:4px;line-height:1.3}

.media-label{position:absolute;top:430px;left:0;right:0;text-align:center;font-size:18px;font-weight:500;letter-spacing:.5px}
.media-glow{position:absolute;top:420px;left:300px;width:600px;height:2px;
  background:linear-gradient(90deg,transparent,rgba(255,255,255,.9),transparent)}

.media-row{position:absolute;top:480px;left:40px;display:flex;gap:24px}
.media-card{width:370px;height:190px;background:var(--card-body);border:1px solid rgba(90,150,230,.35)}
.media-card header{background:var(--bar-blue);height:60px;display:flex;align-items:center;padding:0 20px;
  font-family:"Barlow Condensed",Arial,sans-serif;font-size:22px;font-weight:700;letter-spacing:.5px}
.media-card .price{padding:14px 20px;font-size:16px;line-height:1.4}

.tab-bar{position:absolute;left:0;right:0;bottom:0;height:130px;background:var(--tab-blue);
  display:flex;justify-content:center;gap:60px;padding-top:20px}
.tab{display:flex;flex-direction:column;align-items:center;gap:8px;font-size:12px;font-weight:700;letter-spacing:.4px}
</style>
</head>
<body>
<div class="app">
  <div class="status-bar">
    <span>Trunel</span>
    <span class="time">5:37 pm</span>
    <span>100%</span>
  </div>

  <div class="nav-bar">
    <span class="location"><b>KIOSK</b>GATE 2 T1 HARBOURTON INTERNATIONAL AIRPORT</span>
    <span class="title">DRIFTLINE</span>
  </div>

  <section class="hero">
    <div class="poster" role="img" aria-label="Film poster artwork for Driftline"></div>
    <div class="details">
      <h1>DRIFTLINE</h1>
      <p class="meta">(M) 2013 USA</p>
      <p class="genre">Action Sci-Fi Mystery</p>
      <p class="cast"><b>Starring:</b> Ren Calloway, Otis Marlowe, Tamsin Ellery</p>
      <h2>PLOT SUMMERY</h2>
      <p class="plot">A veteran assigned to extracts Earth's remaining resources begins to question what he knows about his mission and himself.</p>
    </div>
  </section>

  <div class="media-glow"></div>
  <p class="media-label">AVAILABLE MEDIA</p>

  <div class="media-row">
    <article class="media-card">
      <header>RENT SD ENGLISH</header>
      <p class="price">Amount: $6.45<br>Rental $5.99 + Airport Surcharge $0.46</p>
    </article>
    <article class="media-card">
      <header>RENT 720 HD ENGLISH</header>
      <p class="price">Amount: $6.45<br>Rental $5.99 + Airport Surcharge $0.46</p>
    </article>
    <article class="media-card">
      <header>RENT 720 HD ENGLISH</header>
      <p class="price">Amount: $6.45<br>Rental $5.99 + Airport Surcharge $0.46</p>
    </article>
  </div>

  <nav class="tab-bar">
    <div class="tab">
      <svg width="44" height="56" viewBox="0 0 44 56" aria-hidden="true">
        <rect x="3" y="3" width="38" height="50" rx="4" fill="#fff" stroke="#0a1f4a" stroke-width="3"/>
        <rect x="8" y="9" width="28" height="36" fill="#2a6fc9"/>
        <path d="M18 20 L29 27 L18 34 Z" fill="#fff"/>
      </svg>
      <span>MY VIEWING</span>
    </div>
    <div class="tab">
      <svg width="40" height="56" viewBox="0 0 40 56" aria-hidden="true">
        <rect x="6" y="2" width="28" height="52" rx="3" fill="#fff" stroke="#0a1f4a" stroke-width="3"/>
        <rect x="11" y="8" width="18" height="16" fill="#0a1f4a"/>
        <rect x="14" y="30" width="12" height="3" fill="#0a1f4a"/>
        <rect x="14" y="37" width="12" height="3" fill="#0a1f4a"/>
      </svg>
      <span>KIOSK</span>
    </div>
  </nav>
</div>
</body>
</html>
```